SaaS Early tech startup business card design

Unique design for experience ecommerce platform company. the business cards will be used by executive members. conformance with color code is required.

```html
<!DOCTYPE html>
<html lang="en">
<head>
<meta charset="utf-8">
<title>novlo — Business Card</title>
<link href="https://fonts.googleapis.com/css2?family=Roboto:wght@300;400;700&display=swap" rel="stylesheet">
<style>
  :root {
    --backdrop: #1c1c1c;
    --card: #2a2829;
    --card-front: #262526;
    --mark-dark: #0d0d0e;
    --brand-blue: #1478b8;
    --brand-teal: #1fbfa6;
    --brand-aqua: #3fd1b8;
    --text-light: #e6e6e6;
    --paper-white: #f7f7f7;
    --text-dark: #2a2829;
  }
  * { margin: 0; padding: 0; box-sizing: border-box; }
  html, body {
    width: 1200px; height: 874px; overflow: hidden;
    background: var(--backdrop);
    font-family: "Roboto", Arial, sans-serif;
  }
  .canvas {
    width: 1200px; height: 874px;
    display: flex; flex-direction: column; align-items: center; justify-content: center;
    gap: 32px;
  }
  .card {
    position: relative;
    width: 600px; height: 343px;
    overflow: hidden;
    box-shadow: 0 14px 30px rgba(0,0,0,0.45);
  }
  .card--front {
    background: var(--card-front);
    display: flex; align-items: center; justify-content: center;
  }
  .front-wordmark {
    font-weight: 700; font-size: 118px; letter-spacing: -2px;
    color: var(--mark-dark); line-height: 1;
  }
  .card--back { background: var(--card); }
  .holder { position: absolute; left: 40px; top: 86px; }
  .holder-name {
    font-weight: 700; font-size: 25px; color: var(--brand-blue); line-height: 1.05;
  }
  .holder-role {
    font-weight: 400; font-size: 15px; color: var(--brand-teal); margin-top: 2px;
  }
  .back-wordmark {
    position: absolute; right: 48px; top: 70px;
    font-weight: 700; font-size: 62px; letter-spacing: -1px;
    color: var(--brand-teal); line-height: 1;
  }
  .divider {
    position: absolute; left: 32px; right: 44px; top: 150px;
    height: 1px; background: var(--brand-blue);
  }
  .contact-list {
    position: absolute; left: 40px; top: 166px; list-style: none;
  }
  .contact-item {
    display: flex; align-items: center; gap: 10px;
    font-weight: 300; font-size: 14px; color: var(--text-light);
    height: 21px;
  }
  .contact-item svg { width: 12px; height: 12px; fill: var(--brand-teal); flex: none; }
  .address {
    position: absolute; right: 44px; top: 166px; text-align: right;
    font-weight: 300; font-size: 14px; line-height: 1.45; color: var(--text-light);
  }
  .footer-band {
    position: absolute; left: 0; bottom: 0; width: 600px; height: 52px;
  }
  .web {
    position: absolute; right: 40px; bottom: 10px;
    font-weight: 400; font-size: 15px; letter-spacing: 1.5px; color: var(--text-dark);
  }
  .web strong { font-weight: 700; }
</style>
</head>
<body>
<main class="canvas">
  <section class="card card--front" aria-label="Card front">
    <span class="front-wordmark">novlo</span>
  </section>

  <section class="card card--back" aria-label="Card back">
    <div class="holder">
      <p class="holder-name">Daniel Reyes</p>
      <p class="holder-role">President</p>
    </div>
    <span class="back-wordmark">novlo</span>
    <div class="divider"></div>

    <ul class="contact-list">
      <li class="contact-item">
        <svg viewBox="0 0 12 12"><path d="M2.5 0.5 L4.5 2.8 L3.4 4.2 Q4.6 6.9 7.6 8.4 L9 7.3 L11.5 9.4 L10.2 11.3 Q4 10.5 0.8 2 Z"/></svg>
        412-708-3361
      </li>
      <li class="contact-item">
        <svg viewBox="0 0 12 12"><path d="M3 0 H9 V12 H3 Z M4 1.5 V9.5 H8 V1.5 Z"/></svg>
        412-708-3394
      </li>
      <li class="contact-item">
        <svg viewBox="0 0 12 12"><path d="M3 1 H9 V4 H11.5 V10.5 H0.5 V4 H3 Z M4 2 V4 H8 V2 Z M2 6 V7 H10 V6 Z"/></svg>
        412-708-3350
      </li>
      <li class="contact-item">
        <svg viewBox="0 0 12 12"><path d="M0.5 2 H11.5 V10 H0.5 Z M1.5 3 L6 6.5 L10.5 3 Z"/></svg>
        hello@novlo.com
      </li>
    </ul>

    <p class="address">218 Harbor View Road<br>Portland, Maine 04101</p>

    <svg class="footer-band" viewBox="0 0 600 52" aria-hidden="false">
      <defs>
        <linearGradient id="bandTones" x1="0" x2="1" y1="0" y2="0">
          <stop offset="0" stop-color="#1fbfa6"/>
          <stop offset="0.3" stop-color="#1478b8"/>
          <stop offset="0.55" stop-color="#2cc7ae"/>
          <stop offset="0.8" stop-color="#1478b8"/>
          <stop offset="1" stop-color="#1fbfa6"/>
        </linearGradient>
      </defs>
      <rect role="img" aria-label="Mosaic band of teal and blue squares" x="0" y="20" width="360" height="14" fill="url(#bandTones)"/>
      <path d="M0 34 H330 Q352 34 362 22 Q372 10 392 10 H600 V52 H0 Z" fill="var(--paper-white)"/>
    </svg>
    <p class="web">www.<strong>novlo</strong>.com</p>
  </section>
</main>
</body>
</html>
```